Velmori Sciences needs high end Label Design for a revolutionary new supplement

We at Velmori Sciences are looking for a brand new Label Design for a first of its kind product called Solvenna. It is the first supplement on the market that treats grief and heartbreak. This product is unisex for both men and woman. We want the New Label to look high end and luxurious using the brand colors which are gold and burgundy. Please feel free to use other colors such as black, white, or gray to go along with it or any other colors if you feel would be a great fit! Velmori Sciences is like the Tarnwick of the supplement world, coming out with new products that will challenge the way people treat different symptoms. To Recap:

1. Product Name: SOLVENNA - the font will play a big roll
2. The Label will be placed on an all white bottle
3. Some parts of the label will be printed with foil to make parts of the label shiny and more attractive. Please keep this in mind when designing.
4. Must use our Logo. I will attach a file of our logo and of the emblem as well. Feel free to use the emblem separately if you have a great idea for it. Please let us know if you need the Logo in a different file type.
5. This all natural herbal supplement in pill form is the first to treat grief and support someone with a broken heart. The consumers purchasing this product will be going through a hard and emotional time. This is a serious product.
6. The manufacturer has included some basic instructions regarding the dye line and file types. Please do your best to meet these. If you cannot meet the guidelines please submit art work anyways. If your design is chosen we will just have the manufacturer replicate the design.

The final label should portray Solvenna and Velmori Sciences as a luxurious brand and product which was made with cutting edge science leading the way with revolutionary ideas. We want customers to feel that the product is worth every penny, because it is. As soon as they receive the product and take one look at the label, I want them to think WOW I made the right choice buying this. I have attached some Label designs that we really liked for your review.

Please feel free to message me with any questions or if you need the Logo in a different file type. Thank you all.
Updates

Please send in more entries while we take a couple days to review, we are still looking for that one design we can work with. We are getting close, thank you all!

Target Market(s)

People going through grief and heartbreak.

Font styles to use
Sans Serif
Script
Other font styles liked:
• Any font that looks good, The font for the name SOLVENNA is very important and will brand it. We hated the font used in the label we received in our first label draft (attached so you can see)

Requirements
Must have
• Must have the company Logo that says the company name
• Must have the colors Gold and Burgundy
• Must have some areas that will be the shiny foil when label is printed.
• Must say "Dietary Supplement" somewhere near the bottom along with "90 Capsules"
• I have attached a Label someone designed for us but were not really happy with. I did like the font the "Dietary supplement" and "90 Capsules" had and also where it was placed. We absolutely HATED the font used for Solvenna.
• Must look at the label design we received from the manufacturer and take into consideration the room needed to write in the directions and all the symbols such as "made in america" and "KMT Facility" Don't worry about adding these in as they will put those in before printing but keep in mind they will be added to the Final Label along with the Supplement Facts.
Nice to have
• Would like to see other colors to go with gold and burgundy suck as black, white, or gray. I have attached some Label designs that I really liked for your reference.
Should not have
• Does not need to have any other legal language, that will be applied by the the manufacturer's graphics team.

```html
<!DOCTYPE html>
<html lang="en">
<head>
<meta charset="utf-8">
<title>Solvenna Label – Velmori Sciences</title>
<link href="https://fonts.googleapis.com/css2?family=Josefin+Sans:wght@300;400&family=Montserrat:wght@400;600&display=swap" rel="stylesheet">
<style>
  :root {
    --page-bg: #f1f1f1;
    --label-grey: #6e6e6e;
    --foil-light: #f6ead8;
    --foil-mid: #ecc6a0;
    --foil-deep: #d99a66;
    --burgundy: #a4262c;
    --ink: #141414;
    --cream-text: #eadfcd;
  }
  * { margin: 0; padding: 0; box-sizing: border-box; }
  html, body {
    width: 1200px;
    height: 1200px;
    overflow: hidden;
    background: var(--page-bg);
  }
  .label {
    position: absolute;
    left: 120px;
    top: 105px;
    width: 960px;
    height: 990px;
    background: var(--label-grey);
    font-family: "Montserrat", sans-serif;
  }
  .label-art {
    position: absolute;
    inset: 0;
    width: 960px;
    height: 990px;
  }
  .label-eyebrow {
    position: absolute;
    top: 50px;
    width: 100%;
    text-align: center;
    font-size: 21px;
    line-height: 26px;
    letter-spacing: 2px;
    color: var(--cream-text);
    font-weight: 400;
  }
  .brand-mark {
    position: absolute;
    top: 226px;
    left: 0;
    width: 100%;
    display: flex;
    flex-direction: column;
    align-items: center;
  }
  .brand-dot {
    width: 72px;
    height: 72px;
    border-radius: 50%;
    background: var(--burgundy);
    margin-bottom: 38px;
  }
  .brand-name {
    font-family: "Josefin Sans", sans-serif;
    font-weight: 400;
    color: var(--burgundy);
    font-size: 34px;
    letter-spacing: 4px;
    line-height: 1.25;
    text-align: center;
  }
  .product-name {
    position: absolute;
    top: 490px;
    width: 100%;
    text-align: center;
    font-family: "Josefin Sans", sans-serif;
    font-weight: 300;
    font-size: 96px;
    letter-spacing: -1px;
    color: var(--ink);
    line-height: 1;
  }
  .count {
    position: absolute;
    top: 880px;
    width: 100%;
    text-align: center;
    color: var(--cream-text);
    line-height: 44px;
  }
  .count-number {
    font-size: 38px;
    font-weight: 600;
    letter-spacing: 1px;
    vertical-align: middle;
  }
  .count-unit {
    font-size: 20px;
    letter-spacing: 2px;
    margin-left: 8px;
    vertical-align: middle;
  }
</style>
</head>
<body>
  <div class="label">
    <svg class="label-art" viewBox="0 0 960 990" xmlns="http://www.w3.org/2000/svg">
      <defs>
        <linearGradient id="foil" x1="0" y1="0" x2="1" y2="0">
          <stop offset="0" stop-color="var(--foil-light)"/>
          <stop offset="0.45" stop-color="var(--foil-mid)"/>
          <stop offset="1" stop-color="var(--foil-deep)"/>
        </linearGradient>
        <linearGradient id="foil-fade" x1="0" y1="0" x2="1" y2="0">
          <stop offset="0" stop-color="#fff" stop-opacity="0"/>
          <stop offset="0.08" stop-color="#fff" stop-opacity="1"/>
          <stop offset="0.92" stop-color="#fff" stop-opacity="1"/>
          <stop offset="1" stop-color="#fff" stop-opacity="0"/>
        </linearGradient>
        <mask id="foil-mask">
          <rect x="37" y="215" width="897" height="513" fill="url(#foil-fade)"/>
        </mask>
      </defs>
      <rect class="foil-stroke" role="img" aria-label="Gold foil brush stroke"
            x="37" y="230" width="897" height="490" rx="30"
            fill="url(#foil)" mask="url(#foil-mask)"/>
      <polygon class="frame-hexagon" fill="none" stroke="var(--ink)" stroke-width="5"
               points="480,148 776,319 776,690 480,842 184,690 184,319"/>
    </svg>

    <p class="label-eyebrow">DIETARY SUPPLEMENT</p>

    <div class="brand-mark">
      <span class="brand-dot"></span>
      <p class="brand-name">VELMORI<br>SCIENCES</p>
    </div>

    <h1 class="product-name">SOLVENNA</h1>

    <p class="count"><span class="count-number">90</span><span class="count-unit">CAPSULES</span></p>
  </div>
</body>
</html>
```